Equipment Finance Specialist I work with companies who need the funds to buy their equipment

I would like a business card that stands out on the shelves. I want to be able to hand it to someone and say WOW. This card should have my logo.
You can put color into it I am very open on design and color

What my company does is we deal with dealerships that sell equipment such as Dump Trucks garbage trucks tractors trailers. Customers get referred to us and depending on their time in business we will ask for the following items

Companies that have been in business for more than two years we have a credit application program up to 250K . With this program we need the following items Credit application filled out(which is what I would like to be able for the customer to click on my website to get.) as well as three current month bank statements.

Deals over 250k we will need the following items

2 years business tax returns
2 years personal tax returns
Profit & Loss statement
Personal Financial Statement

what we do
100% FINANCING
SEASONAL PAYMENTS
LOAN BALLOON PAYMENTS
TRAC LEASING
LOW-INTEREST REFINANCING RATES
DEBT CONSOLIDATION

We specialize in creative financing solutions and offer a variety of reliable, flexible and expandable lending choices.

Target Market(s)

Trucking Companies

Industry/Entity Type

Trucking Company

Contact Information for Business Card

* $250,000 Application only Program
* Loans from $30,000 to 5,000,000
* Competitive Interest Rates

Font styles to use
Serif
Sans Serif

Colors

Designer to choose colors to be used in the design.

Requirements
Must have
• On the back of the card.
• * $250,000 Application only Program
• * Loans from $30,000 to 5,000,000
• My name, email, website. address
• * Competitive Interest Rates
• * 100% Financing
Nice to have
• I want my logo to pop on the card
• My logo is the great one I would like to use
Should not have
• I am up for your creativity as well

```html
<!DOCTYPE html>
<html lang="en">
<head>
<meta charset="utf-8">
<title>Ridgeline Funding – Business Card</title>
<link rel="stylesheet" href="https://fonts.googleapis.com/css2?family=Open+Sans:wght@400;600;700&display=swap">
<style>
  :root {
    --backdrop: #4a3c36;
    --card: #1b1b1c;
    --ink: #f2f2f2;
    --silver: #c9c9c9;
    --rule: #8a8a8a;
  }
  * { margin: 0; padding: 0; box-sizing: border-box; }
  html, body { width: 1200px; height: 864px; overflow: hidden; }
  body {
    background: var(--backdrop);
    font-family: "Open Sans", sans-serif;
    display: flex;
    align-items: center;
    justify-content: center;
    gap: 40px;
  }
  .card {
    width: 540px;
    height: 309px;
    background: var(--card);
    color: var(--ink);
    border-radius: 4px;
    box-shadow: 0 10px 24px rgba(0,0,0,.35);
    position: relative;
  }
  /* Front: brand + program highlights */
  .card--front {
    display: flex;
    flex-direction: column;
    align-items: center;
    justify-content: center;
    gap: 34px;
  }
  .brand-name {
    font-weight: 700;
    font-size: 38px;
    letter-spacing: 2px;
    color: var(--silver);
    text-transform: uppercase;
    text-align: center;
    line-height: 1.05;
  }
  .brand-name small {
    display: block;
    font-size: 22px;
    letter-spacing: 6px;
  }
  .highlights {
    list-style: none;
    text-align: center;
    font-size: 14px;
    line-height: 1.5;
    color: var(--ink);
  }
  /* Back: mark + contact */
  .card--back {
    display: flex;
    align-items: center;
    padding: 0 36px;
  }
  .brand-mark {
    width: 190px;
    display: flex;
    align-items: center;
    gap: 10px;
  }
  .brand-mark .dot {
    width: 22px; height: 22px;
    border-radius: 50%;
    background: var(--ink);
    flex-shrink: 0;
  }
  .brand-mark span {
    font-weight: 700;
    font-size: 19px;
    letter-spacing: 1px;
    text-transform: uppercase;
    line-height: 1.15;
  }
  .divider {
    width: 1px;
    height: 190px;
    background: var(--rule);
    margin: 0 26px 0 20px;
  }
  .contact { font-size: 14px; line-height: 1.35; }
  .contact .name { font-weight: 700; font-size: 19px; letter-spacing: .5px; }
  .contact .role { font-size: 14px; margin-bottom: 12px; }
  .contact .address { margin-bottom: 6px; }
  .contact-line { display: flex; align-items: center; gap: 8px; }
  .contact-line svg { width: 12px; height: 12px; fill: var(--ink); flex-shrink: 0; }
  .contact-line.plain { padding-left: 20px; }
</style>
</head>
<body>
  <section class="card card--front">
    <h1 class="brand-name">Ridgeline<small>Funding</small></h1>
    <ul class="highlights">
      <li>$250,000 Application only Program ● Loans from $30,000 to 5,000,000</li>
      <li>Competitive Interest Rates ● 100% Financing</li>
    </ul>
  </section>

  <section class="card card--back">
    <div class="brand-mark">
      <div class="dot"></div>
      <span>Ridgeline<br>Funding</span>
    </div>
    <div class="divider"></div>
    <div class="contact">
      <div class="name">MARK ALDEN</div>
      <div class="role">PRESIDENT</div>
      <div class="address">412 Harbor Lane<br>Millbrook, NY 12545</div>
      <div class="contact-line">
        <svg viewBox="0 0 24 24" aria-hidden="true"><path d="M6.6 10.8a15.1 15.1 0 0 0 6.6 6.6l2.2-2.2a1 1 0 0 1 1-.25 11.4 11.4 0 0 0 3.6.57 1 1 0 0 1 1 1V20a1 1 0 0 1-1 1A17 17 0 0 1 3 4a1 1 0 0 1 1-1h3.5a1 1 0 0 1 1 1c0 1.25.2 2.45.57 3.6a1 1 0 0 1-.25 1z"/></svg>
        555 0142 7788
      </div>
      <div class="contact-line">
        <svg viewBox="0 0 24 24" aria-hidden="true"><path d="M2 5h20v14H2zm2 2v.5l8 5 8-5V7z"/></svg>
        mark@ridgelinefunding.com
      </div>
      <div class="contact-line">
        <svg viewBox="0 0 24 24" aria-hidden="true"><circle cx="12" cy="12" r="10"/></svg>
        www.ridgelinefunding.com
      </div>
      <div class="contact-line plain">www.ridgelinefunding.com</div>
    </div>
  </section>
</body>
</html>
```